Granite Bureau of Analysis Card Design

I need a business card for the agency I currently am tasked with, which is based in Hartford, CT. GBAN provides, disseminates and obtains intelligence in regards to ongoing criminal investigations throughout the State of CT. The information we obtain and provide, comes to us and is sent out by various Law Enforcement agencies throughout CT.

Industry/Entity Type

Business

Contact Information for Business Card

Officer Lyle P. Harrowby
Bramford Police Department - Eastern Region Intelligence Officer
Granite Bureau of Analysis
4827 Willowmere Ave., Middletown, CT 06457
Work Cell: (555) 318-2694
E-Mail: gban.wd@gbanmail.example

```html
<!DOCTYPE html>
<html lang="en">
<head>
<meta charset="utf-8">
<title>Granite Bureau of Analysis — Business Card</title>
<link href="https://fonts.googleapis.com/css2?family=Exo+2:wght@400;500;600&display=swap" rel="stylesheet">
<style>
  :root {
    --backdrop: #e4e4e4;
    --card: #ffffff;
    --red: #b82a27;
    --yellow: #e2cc37;
    --ink: #2b2b2b;
    --name-red: #c3302b;
  }
  * { margin: 0; padding: 0; box-sizing: border-box; }
  html, body {
    width: 1200px; height: 900px; overflow: hidden;
    background: var(--backdrop);
    font-family: "Exo 2", Arial, sans-serif;
  }
  .stage {
    width: 1200px; height: 900px;
    display: flex; align-items: center; justify-content: center;
  }
  .card {
    position: relative;
    width: 900px; height: 514px;
    background: var(--card);
    box-shadow: 0 10px 30px rgba(0,0,0,0.18);
    overflow: hidden;
  }
  .card__swoosh { position: absolute; inset: 0; }
  .brand {
    position: absolute; left: 70px; top: 165px;
    display: flex; align-items: center; gap: 14px;
    font-weight: 600; font-size: 30px; line-height: 1.15; color: var(--ink);
    letter-spacing: 1px; text-transform: uppercase;
  }
  .brand__mark { width: 22px; height: 22px; background: var(--red); flex: none; }
  .identity {
    position: absolute; right: 82px; top: 46px; text-align: right;
  }
  .identity__name {
    color: var(--name-red); font-weight: 500; font-size: 34px;
    letter-spacing: 2px; text-transform: uppercase; line-height: 1.1;
  }
  .identity__title { color: var(--ink); font-size: 20px; letter-spacing: 0.5px; line-height: 1.3; }
  .identity__tab {
    position: absolute; right: 0; top: 48px;
    width: 54px; height: 26px; background: var(--yellow);
  }
  .contacts {
    position: absolute; right: 40px; top: 180px;
    list-style: none; text-align: right;
  }
  .contacts li {
    display: flex; justify-content: flex-end; align-items: center; gap: 12px;
    color: var(--ink); font-size: 18px; letter-spacing: 1px; height: 38px;
  }
  .contacts svg { width: 20px; height: 20px; flex: none; }
  .address {
    position: absolute; left: 36px; bottom: 34px;
    color: #fff; font-size: 24px; line-height: 1.3; letter-spacing: 1px;
    font-style: normal;
  }
</style>
</head>
<body>
<main class="stage">
  <section class="card">
    <svg class="card__swoosh" viewBox="0 0 900 514" preserveAspectRatio="none" aria-hidden="true">
      <path d="M470,455 C640,420 790,360 900,300 L900,318 C790,378 640,440 470,462 Z" fill="var(--yellow)"/>
      <path d="M0,300 C230,470 600,475 900,372 L900,514 L0,514 Z" fill="var(--red)"/>
    </svg>

    <div class="brand">
      <span class="brand__mark"></span>
      <span>Bramford Police<br>Department</span>
    </div>

    <span class="identity__tab"></span>
    <header class="identity">
      <h1 class="identity__name">Lyle P. Harrowby</h1>
      <p class="identity__title">Eastern Region Intelligence Officer</p>
      <p class="identity__title">Granite Bureau of Analysis</p>
    </header>

    <ul class="contacts">
      <li>(555) 318-2694
        <svg viewBox="0 0 20 20"><rect x="5" y="1.5" width="10" height="17" rx="2" fill="none" stroke="var(--red)" stroke-width="2"/><circle cx="10" cy="15.5" r="1" fill="var(--red)"/></svg>
      </li>
      <li>gban.wd@gbanmail.example
        <svg viewBox="0 0 20 20"><rect x="2" y="4" width="16" height="12" fill="var(--red)"/><path d="M2 4l8 7 8-7" fill="none" stroke="#fff" stroke-width="1.5"/></svg>
      </li>
    </ul>

    <address class="address">
      4827 Willowmere Ave.,<br>Middletown, CT 06457
    </address>
  </section>
</main>
</body>
</html>
```